Tolbek cards

I want a simple business card that pops.
Logo on one side.
On side two i want.
"Are you thinking about a new building on your property, or renovating an existing structure? Contact".....
Owners Name: Dale Whitacre
Owners Phone number: 610-555-0187
Address:4076 Copper Ridge RD, Millbrook, PA 17480
Committed to Quality, Service, and Integrity

```html
<!DOCTYPE html>
<html lang="en">
<head>
<meta charset="utf-8">
<title>Tolbek Builders LLC – Business Cards</title>
<link rel="stylesheet" href="https://fonts.googleapis.com/css2?family=Arimo:ital,wght@0,400;0,700;1,700&display=swap">
<style>
  :root {
    --backdrop: #5b5b5b;
    --walnut: #422e1d;
    --cocoa: #5a3d27;
    --tan-light: #a28c70;
    --tan-dark: #7d6148;
    --paper: #ffffff;
  }
  * { margin: 0; padding: 0; box-sizing: border-box; }
  html, body {
    width: 1200px; height: 1200px; overflow: hidden;
    background: var(--backdrop);
    font-family: "Arimo", Arial, sans-serif;
  }
  .card {
    position: absolute;
    width: 690px; height: 394px;
    background: var(--paper);
    overflow: hidden;
  }
  .card-front { left: 266px; top: 158px; }
  .card-back { left: 260px; top: 651px; }
  .card-shapes { position: absolute; inset: 0; width: 100%; height: 100%; }

  .pitch {
    position: absolute; left: 26px; top: 48px; width: 250px;
    color: var(--cocoa);
    font-weight: 700; font-style: italic;
    font-size: 18.5px; line-height: 24px;
    letter-spacing: 0.2px;
  }
  .brand {
    position: absolute;
    display: flex; align-items: center; gap: 12px;
    color: var(--walnut);
    font-weight: 700;
  }
  .brand-mark { background: var(--walnut); flex: none; }
  .brand-front { left: 26px; top: 215px; width: 240px; font-size: 30px; line-height: 34px; }
  .brand-front .brand-mark { width: 30px; height: 30px; }
  .brand-back { left: 0; right: 0; top: 0; bottom: 0; justify-content: center; font-size: 44px; }
  .brand-back .brand-mark { width: 44px; height: 44px; }

  .details {
    position: absolute; right: 28px; top: 0;
    text-align: right; color: var(--paper);
  }
  .tagline { position: absolute; right: 0; top: 51px; white-space: nowrap; font-size: 17.5px; }
  .owner-name { position: absolute; right: 0; top: 190px; white-space: nowrap; font-size: 25px; font-weight: 700; letter-spacing: 0.3px; }
  .phone {
    position: absolute; right: 0; top: 262px; white-space: nowrap;
    font-size: 16.5px; display: flex; align-items: center; gap: 12px;
  }
  .phone svg { width: 15px; height: 15px; }
  .address { position: absolute; right: 0; top: 295px; white-space: nowrap; font-size: 16.5px; line-height: 21px; }
</style>
</head>
<body>

<section class="card card-front">
  <svg class="card-shapes" viewBox="0 0 1108 633" preserveAspectRatio="none" aria-hidden="true">
    <defs>
      <linearGradient id="tan-front" x1="0" x2="1" y1="0" y2="0">
        <stop offset="0" stop-color="var(--tan-light)"/>
        <stop offset="0.55" stop-color="var(--tan-dark)"/>
        <stop offset="1" stop-color="var(--tan-light)"/>
      </linearGradient>
    </defs>
    <polygon points="436,0 1108,0 1108,633 579,633" fill="var(--walnut)"/>
    <polygon points="498,275 442,633 579,633" fill="url(#tan-front)"/>
  </svg>

  <p class="pitch">Are you thinking about a new building on your property, or renovating an existing structure?</p>

  <div class="brand brand-front">
    <span class="brand-mark"></span>
    <span>Tolbek<br>Builders LLC</span>
  </div>

  <div class="details">
    <p class="tagline">Committed to Quality, Service, and Integrity</p>
    <p class="owner-name">DALE WHITACRE</p>
    <p class="phone">610-555-0187
      <svg viewBox="0 0 24 24" aria-hidden="true"><path fill="currentColor" d="M6.6 10.8a15.1 15.1 0 0 0 6.6 6.6l2.2-2.2a1 1 0 0 1 1-.25 11.4 11.4 0 0 0 3.6.57 1 1 0 0 1 1 1V20a1 1 0 0 1-1 1A17 17 0 0 1 3 4a1 1 0 0 1 1-1h3.5a1 1 0 0 1 1 1c0 1.25.2 2.45.57 3.57a1 1 0 0 1-.25 1z"/></svg>
    </p>
    <p class="address">4076 Copper Ridge RD<br>Millbrook, PA 17480</p>
  </div>
</section>

<section class="card card-back">
  <svg class="card-shapes" viewBox="0 0 1114 636" preserveAspectRatio="none" aria-hidden="true">
    <defs>
      <linearGradient id="tan-back" x1="0" x2="1" y1="0" y2="0">
        <stop offset="0" stop-color="var(--tan-dark)"/>
        <stop offset="1" stop-color="var(--tan-light)"/>
      </linearGradient>
    </defs>
    <polygon points="0,0 102,0 40,270 0,110" fill="url(#tan-back)"/>
    <polygon points="0,110 40,270 125,636 0,636" fill="var(--walnut)"/>
    <polygon points="1013,0 1114,0 1114,110 1074,270" fill="url(#tan-back)"/>
    <polygon points="1114,110 1114,636 991,636 1074,270" fill="var(--walnut)"/>
  </svg>

  <div class="brand brand-back">
    <span class="brand-mark"></span>
    <span>Tolbek Builders LLC</span>
  </div>
</section>

</body>
</html>
```